Stylish High End Wedding Videography/Films Website (BMRT)

We need a modern and high-end website look for our wedding video and films business. We films weddings all over the United Kingdom and at European destinations so need something to reflect our work. The website should be visually stunning with images and videos being the focal point as this is what our services are;

I have uploads of some items I like and the features the site needs to have. These have been taken from other websites using standout features.

We need the following pages;

1 - Homepage
2 - Films Index Page
3 - Individual Films Page
4 - Prices / Collection Page
5 - Reviews
6 - Options
7 - About
8 - Contact
9 - Blog Index
10 - Blog Page

All pages must be consistent so have a similar style.

Pages on menu:
Films
Prices
Reviews
Options
About
Contact

We require a responsive look too. Over 90% of our visitors access the website via their mobile devices.

Please use the colours from our logo to incorporate into the website.

Target Market(s)

Wedding Couples

Industry/Entity Type

Wedding Photography

Number of Pages Required

5+ page

Font styles to use
Sans Serif
Script

Requirements
Must have
• The logo must be in the centre of the menu at the top.

Social icons at the bottom of the page.

Use only two fonts including Lore which is supplied
Nice to have
• Different video for each page on the top header. This will play behind the menu.

```html
<!DOCTYPE html>
<html lang="en">
<head>
<meta charset="utf-8">
<title>BMRT Wedding Films</title>
<link rel="stylesheet" href="https://fonts.googleapis.com/css2?family=Josefin+Sans:wght@300;400;600&family=Mrs+Saint+Delafield&display=swap">
<style>
:root{
  --gold:#8c7a4f;
  --gold-soft:#a8956a;
  --brown:#6b5838;
  --ink:#2b2a28;
  --white:#ffffff;
  --paper:#ffffff;
  --rule:#d8d2c4;
  --icon:#5b5b5b;
}
*{margin:0;padding:0;box-sizing:border-box}
html,body{width:1200px;height:3774px;overflow:hidden;background:var(--paper)}
body{position:relative;font-family:"Josefin Sans",sans-serif;color:var(--ink)}
.abs{position:absolute}
.script{font-family:"Mrs Saint Delafield",cursive;font-weight:400}
.photo{position:absolute}

/* hero */
.hero{left:0;top:0;width:1200px;height:667px;
  background:
    radial-gradient(ellipse 420px 200px at 620px 300px,rgba(240,236,228,.28),transparent 70%),
    radial-gradient(ellipse 500px 180px at 300px 60px,rgba(214,132,60,.55),transparent 70%),
    radial-gradient(ellipse 380px 140px at 980px 90px,rgba(196,110,52,.45),transparent 70%),
    linear-gradient(180deg,#5e3c2a 0%,#7a4a2e 22%,#4e3a2c 48%,#2e261e 75%,#1f1a14 100%)}
.brand{left:0;width:1200px;text-align:center;color:var(--white)}
.brand-mark{left:586px;top:34px;width:28px;height:28px;border:2px solid var(--white);border-radius:50%}
.brand-name{top:82px;font-size:15px;letter-spacing:4px;font-weight:600}
.brand-sub{top:101px;font-size:7px;letter-spacing:4px}
.nav a{position:absolute;top:140px;color:var(--white);font-size:15px;text-decoration:none;letter-spacing:.5px;transform:translateX(-50%)}
.nav-frame{left:182px;top:122px;width:52px;height:51px}
.play{left:565px;top:278px}
.hero-title{top:368px;left:0;width:1200px;text-align:center;color:var(--white);font-size:74px}
.hero-tag{top:470px;left:0;width:1200px;text-align:center;color:var(--white);font-size:17px;letter-spacing:19px;font-weight:300}
.dots{left:572px;top:617px}

/* about */
.about-photo{left:0;top:667px;width:1200px;height:772px;
  background:
    radial-gradient(ellipse 260px 360px at 470px 520px,rgba(34,30,28,.55),transparent 70%),
    radial-gradient(ellipse 240px 330px at 880px 500px,rgba(250,246,238,.55),transparent 70%),
    linear-gradient(180deg,#e4ebe9 0%,#cfc8b2 18%,#c09457 42%,#a56e35 70%,#7a4b22 100%)}
.section-title{left:0;width:1200px;text-align:center;font-size:74px;color:var(--ink)}
.about-title{top:676px}
.about-box{left:130px;top:779px;width:934px;height:175px;background:rgba(255,255,255,.72);display:flex;align-items:center;justify-content:center;padding:0 40px}
.copy{font-size:12.5px;line-height:19px;color:var(--brown);text-align:center;font-variant:small-caps;letter-spacing:.3px}

/* films grid */
.tile{position:absolute}
.t1{left:0;top:1439px;width:599px;height:652px;
  background:
    radial-gradient(ellipse 180px 280px at 250px 360px,rgba(60,44,34,.7),transparent 70%),
    radial-gradient(ellipse 150px 220px at 470px 380px,rgba(220,206,180,.45),transparent 70%),
    linear-gradient(165deg,#5c5c62 0%,#6a5d52 45%,#4e3c2c 100%)}
.t2{left:599px;top:1439px;width:601px;height:439px;
  background:
    radial-gradient(ellipse 200px 160px at 220px 260px,rgba(238,230,222,.55),transparent 70%),
    radial-gradient(ellipse 180px 200px at 430px 240px,rgba(40,34,32,.6),transparent 70%),
    linear-gradient(150deg,#9a9284 0%,#6f645a 50%,#3c3632 100%)}
.t3{left:599px;top:1878px;width:601px;height:438px;
  background:
    radial-gradient(ellipse 140px 220px at 300px 300px,rgba(242,236,230,.6),transparent 70%),
    radial-gradient(ellipse 80px 200px at 170px 200px,rgba(30,28,28,.6),transparent 70%),
    linear-gradient(110deg,#4e4944 0%,#7e7872 40%,#d6d2ca 75%,#9a968e 100%)}
.t4{left:0;top:2091px;width:599px;height:669px;
  background:
    radial-gradient(ellipse 130px 320px at 360px 420px,rgba(236,232,222,.55),transparent 70%),
    radial-gradient(ellipse 400px 160px at 300px 80px,rgba(226,176,100,.55),transparent 70%),
    linear-gradient(180deg,#b88c52 0%,#a0855a 40%,#857458 75%,#5e5648 100%)}
.t5{left:599px;top:2316px;width:601px;height:444px;
  background:
    radial-gradient(ellipse 200px 160px at 420px 300px,rgba(168,110,80,.35),transparent 70%),
    linear-gradient(140deg,#8e7c56 0%,#9e8c64 50%,#7c6a46 100%)}
.tile-label{position:absolute;color:var(--white);font-size:23px;font-weight:600;text-decoration:underline;text-underline-offset:4px;letter-spacing:.3px}
.tile-text{position:absolute;color:var(--white);font-size:13px;line-height:20px;font-variant:small-caps}

/* reviews */
.reviews-title{top:2796px}
.review-box{left:130px;top:2899px;width:934px;height:199px;
  background:
    radial-gradient(ellipse 220px 120px at 240px 60px,rgba(230,220,190,.35),transparent 70%),
    radial-gradient(ellipse 200px 120px at 760px 120px,rgba(120,100,60,.3),transparent 70%),
    linear-gradient(90deg,#a39168,#b5a37a 50%,#a08e64)}
.avatar{left:555px;top:2889px;width:88px;height:88px;border-radius:50%;border:3px solid var(--white);
  background:radial-gradient(circle at 38% 45%,#f2ece4 0 28%,transparent 30%),linear-gradient(150deg,#d8cfc0,#5e5044)}
.review-copy{left:150px;top:2991px;width:894px;color:var(--white)}
.review-name{left:0;top:3066px;width:1200px;text-align:center;color:var(--white);font-size:14px;font-weight:600}

/* instagram */
.insta-title{position:absolute;left:0;top:3192px;width:1200px;text-align:center;font-size:25px;letter-spacing:1px;font-weight:400}
.thumb{position:absolute;width:145px}

/* footer */
.foot{font-size:15px;color:var(--ink)}
.foot-mark{left:578px;top:3496px;width:42px;height:42px;border:2px solid var(--gold);border-radius:50%}
.foot-name{left:0;top:3557px;width:1200px;text-align:center;color:var(--brown);font-size:19px;letter-spacing:6px}
.foot-sub{left:0;top:3581px;width:1200px;text-align:center;color:var(--brown);font-size:9px;letter-spacing:5px}
.social{position:absolute;top:3556px;width:28px;height:28px}
.rule{left:0;top:3692px;width:1200px;height:1px;background:var(--rule)}
.copyright{left:0;top:3724px;width:1200px;text-align:center;font-size:11px;color:var(--brown);font-variant:small-caps;letter-spacing:.5px}
</style>
</head>
<body>

<!-- hero -->
<div class="photo hero" role="img" aria-label="Couple sitting by a lake at sunset, background video"></div>
<div class="abs brand-mark"></div>
<div class="abs brand brand-name">BMRT</div>
<div class="abs brand brand-sub">WEDDING FILMS</div>
<svg class="abs nav-frame" viewBox="0 0 52 51" fill="none" stroke="#c9b98c" stroke-width="3">
  <path d="M1 14V1h13M38 1h13v13M51 37v13H38M14 50H1V37"/>
</svg>
<nav class="nav">
  <a style="left:208px">HOME</a>
  <a style="left:328px">ABOUT</a>
  <a style="left:456px">FILMS</a>
  <a style="left:571px">PRICES</a>
  <a style="left:699px">OPTIONS</a>
  <a style="left:834px">REVIEWS</a>
  <a style="left:973px">CONTACT</a>
</nav>
<svg class="abs play" width="68" height="68" viewBox="0 0 68 68" fill="none" stroke="#fff" stroke-width="2">
  <circle cx="34" cy="34" r="32"/><path d="M26 20l22 14-22 14z"/>
</svg>
<div class="abs script hero-title">BMRT Films</div>
<div class="abs hero-tag">WHAT&nbsp;&nbsp; WE&nbsp;&nbsp; DELIVER</div>
<svg class="abs dots" width="56" height="12" viewBox="0 0 56 12">
  <circle cx="6" cy="6" r="5" fill="#fff"/>
  <circle cx="28" cy="6" r="4.5" fill="none" stroke="#fff" stroke-width="1.2"/>
  <circle cx="50" cy="6" r="4.5" fill="none" stroke="#fff" stroke-width="1.2"/>
</svg>

<!-- about -->
<section>
  <div class="photo about-photo" role="img" aria-label="Bride and groom walking hand in hand through a golden field"></div>
  <h2 class="abs script section-title about-title">About Us</h2>
  <div class="abs about-box">
    <p class="copy">Your wedding day is a once in a lifetime moment. A moment in time where all the people you love and care about are in the same place at the same time. We document unique moments on film. The laughs, the tears and the love. The films we make will last a lifetime. They will be shown to future generations and will become an heirloom. It will be watched over and over again over the years. Your memories of your day will fade however our wedding films will ensure you never forgot those moments.</p>
  </div>
</section>

<!-- films -->
<section>
  <div class="tile t1" role="img" aria-label="Groom holding bride's face by a lake"></div>
  <div class="tile t2" role="img" aria-label="Bride in flower crown embracing a guest"></div>
  <div class="tile t3" role="img" aria-label="Bride by a window with groom in the background"></div>
  <div class="tile t4" role="img" aria-label="Couple standing in a field beside a wooden cart"></div>
  <div class="tile t5" role="img" aria-label="Soft faded wedding flowers photo"></div>

  <div class="tile-label" style="left:59px;top:1942px">CINEMATIC HIGHLIGHTS FILM</div>
  <p class="tile-text" style="left:59px;top:1994px;width:360px">A highlights film, a harmony of moving imagery, vocals and music, which is unique to you.</p>
  <svg class="abs" style="left:480px;top:1999px" width="48" height="24" viewBox="0 0 48 24" fill="none" stroke="#fff" stroke-width="1.5">
    <path d="M0 12h46M36 2l10 10-10 10"/>
  </svg>

  <div class="tile-label" style="left:669px;top:1819px">CEREMONY AND SPEECHES</div>
  <div class="tile-label" style="left:669px;top:2238px">EXTENDED DOCUMENTARY FILM</div>
  <div class="tile-label" style="left:59px;top:2677px">OUR STORY FEATURE</div>

  <svg class="abs" style="left:846px;top:2474px" width="104" height="104" viewBox="0 0 104 104" fill="none" stroke="#fff" stroke-width="2.5">
    <circle cx="52" cy="52" r="50"/><path d="M28 52h48M60 36l16 16-16 16"/>
  </svg>
  <div class="tile-label" style="left:851px;top:2631px">VIEW ALL</div>
</section>

<!-- reviews -->
<section>
  <h2 class="abs script section-title reviews-title">Client Reviews</h2>
  <div class="abs review-box" role="img" aria-label="Faded photo of wedding rings behind the review"></div>
  <div class="abs avatar" role="img" aria-label="Client couple portrait"></div>
  <p class="abs copy review-copy">Your wedding day is a once in a lifetime moment. A moment in time where all the people you love and care about are in the same place at the same time. We document unique moments on film. The laughs, the tears and the love. The films we make will last a lifetime. They will be shown to future generations and will become an heirloom. It will be watched over and over again over the years.</p>
  <div class="abs review-name">- HANNAH REID</div>
  <svg class="abs" style="left:70px;top:2978px" width="52" height="28" viewBox="0 0 52 28" fill="none" stroke="#999" stroke-width="1.5">
    <path d="M52 14H2M14 2L2 14l12 12"/>
  </svg>
  <svg class="abs" style="left:1080px;top:2978px" width="52" height="28" viewBox="0 0 52 28" fill="none" stroke="#999" stroke-width="1.5">
    <path d="M0 14h50M38 2l12 12-12 12"/>
  </svg>
</section>

<!-- instagram -->
<section>
  <h2 class="insta-title">FOLLOW US ON INSTAGRAM</h2>
  <div class="thumb" style="left:108px;top:3261px;height:171px;background:radial-gradient(ellipse 50px 70px at 70px 100px,#f4f2ec,transparent 75%),linear-gradient(160deg,#c8cabe,#7e8478)" role="img" aria-label="Bride holding a bouquet"></div>
  <div class="thumb" style="left:275px;top:3275px;height:143px;background:radial-gradient(ellipse 60px 40px at 72px 72px,#d6b8a4,transparent 75%),linear-gradient(160deg,#ece6de,#c8b4a4)" role="img" aria-label="Couple's hands with rings"></div>
  <div class="thumb" style="left:444px;top:3261px;height:171px;background:radial-gradient(ellipse 40px 60px at 50px 110px,#d8d4ce,transparent 75%),linear-gradient(160deg,#6a6460,#2e2a28)" role="img" aria-label="Couple embracing in black and white"></div>
  <div class="thumb" style="left:611px;top:3275px;height:143px;background:radial-gradient(ellipse 40px 40px at 95px 70px,#c66e5e,transparent 75%),linear-gradient(160deg,#ece2da,#c09a8a)" role="img" aria-label="Bride holding pink flowers"></div>
  <div class="thumb" style="left:779px;top:3261px;height:171px;background:radial-gradient(ellipse 40px 60px at 110px 110px,#f0ece8,transparent 75%),linear-gradient(160deg,#c8d0c4,#34405a)" role="img" aria-label="Groom in blue suit with bride"></div>
  <div class="thumb" style="left:946px;top:3275px;height:143px;background:radial-gradient(ellipse 45px 50px at 100px 90px,#f4f0ea,transparent 75%),linear-gradient(160deg,#8e9e78,#d8d0c4)" role="img" aria-label="Couple laughing outdoors"></div>
</section>

<!-- footer -->
<footer>
  <div class="abs foot" style="left:143px;top:3527px">07700 900 214</div>
  <div class="abs foot" style="left:95px;top:3573px;font-size:12px">info@bmrtfilms.co.uk</div>
  <div class="abs foot-mark"></div>
  <div class="abs foot-name">BMRT</div>
  <div class="abs foot-sub">WEDDING FILMS</div>

  <svg class="social" style="left:946px" viewBox="0 0 28 28" role="img" aria-label="Email">
    <circle cx="14" cy="14" r="14" fill="var(--icon)"/>
    <rect x="7" y="9" width="14" height="10" fill="none" stroke="#fff" stroke-width="1.5"/>
    <path d="M7 9l7 6 7-6" fill="none" stroke="#fff" stroke-width="1.5"/>
  </svg>
  <svg class="social" style="left:988px" viewBox="0 0 28 28" role="img" aria-label="Phone">
    <circle cx="14" cy="14" r="14" fill="var(--icon)"/>
    <path d="M10 7l3 3-2 2c1 2 3 4 5 5l2-2 3 3-2 3c-5 0-12-7-12-12z" fill="#fff"/>
  </svg>
  <svg class="social" style="left:1029px" viewBox="0 0 28 28" role="img" aria-label="Location">
    <circle cx="14" cy="14" r="14" fill="var(--icon)"/>
    <path d="M14 6a5 5 0 0 1 5 5c0 4-5 10-5 10s-5-6-5-10a5 5 0 0 1 5-5z" fill="#fff"/>
    <circle cx="14" cy="11" r="2" fill="var(--icon)"/>
  </svg>
  <svg class="social" style="left:1073px" viewBox="0 0 28 28" role="img" aria-label="Watch our films">
    <circle cx="14" cy="14" r="14" fill="var(--icon)"/>
    <path d="M11 8l9 6-9 6z" fill="#fff"/>
  </svg>

  <div class="abs rule"></div>
  <div class="abs copyright">Copyright © 2020 BMRT Wedding Films Limited. All rights reserved.</div>
</footer>

</body>
</html>
```